Harbourline Physiotherapy business card design

We need a fresh, new business card design for our physiotherapy clinic Harbourline Physiotherapy

Will attach logo soon we had logo designed from our last project

Industry/Entity Type

Physical Therapy

Contact Information for Business Card

On front
Needs our logo, contact details:
58 Wexley Lane Kelverton NSW 2841
Ph/f: 02 9481 2057
info@harbourlinephysio.example.com.au

Requirements
Must have
• On the back of the card needs to have area to write down follow up appointments
• On front
• Needs our logo
• The colours have to be the colours in our logo which are: sky blue, black and white
• Font to be same as our logo please
• We want the card to look simple, not too cluttered but to the point
Should not have
• We don't need any extra pictures other than our logo

```html
<!DOCTYPE html>
<html lang="en">
<head>
<meta charset="utf-8">
<title>Harbourline Physiotherapy – Business Card</title>
<link rel="stylesheet" href="https://fonts.googleapis.com/css2?family=Source+Sans+3:ital,wght@0,400;0,600;0,700;1,400&display=swap">
<style>
  :root {
    --backdrop: #4d4d4d;
    --card: #ffffff;
    --sky: #1d6fd1;
    --navy: #1a3fae;
    --ink: #3a3a3a;
    --rule: #555555;
  }
  * { box-sizing: border-box; margin: 0; padding: 0; }
  html, body { width: 1105px; height: 1200px; overflow: hidden; }
  body {
    background: var(--backdrop);
    font-family: "Source Sans 3", "Myriad Pro", Arial, sans-serif;
    position: relative;
  }
  .card {
    position: absolute;
    left: 196px;
    width: 720px;
    height: 412px;
    background: var(--card);
    border-radius: 20px;
  }
  .card--front { top: 146px; }
  .card--back { top: 602px; }

  /* Front */
  .brand {
    position: absolute;
    right: 25px;
    top: 60px;
    display: flex;
    align-items: center;
    gap: 14px;
  }
  .brand__dot {
    width: 40px; height: 40px;
    border-radius: 50%;
    background: var(--sky);
  }
  .brand__name {
    color: var(--sky);
    font-weight: 600;
    font-size: 30px;
    line-height: 1.05;
  }
  .contact {
    position: absolute;
    left: 28px;
    top: 202px;
    color: var(--ink);
    font-size: 19px;
    line-height: 1;
  }
  .contact__name {
    color: var(--sky);
    font-weight: 600;
    font-size: 27px;
    margin-bottom: 9px;
  }
  .contact__role { font-size: 20px; margin-bottom: 20px; }
  .contact__line { margin-bottom: 10px; }
  .contact__label { color: var(--sky); font-weight: 700; margin-right: 6px; }
  .contact__address { margin-top: 14px; }

  /* Back */
  .appointment__title {
    position: absolute;
    top: 28px; left: 0; right: 0;
    text-align: center;
    color: var(--navy);
    font-weight: 700;
    font-size: 27px;
  }
  .field {
    position: absolute;
    border-bottom: 1.5px solid var(--rule);
    color: var(--navy);
    font-size: 20px;
    line-height: 1;
    padding-bottom: 6px;
  }
  .field--for { left: 48px; width: 619px; top: 76px; }
  .field--date { left: 46px; width: 331px; top: 133px; }
  .field--time { left: 405px; width: 261px; top: 133px; }
  .field--doctor { left: 48px; width: 619px; top: 191px; }
  .field--note { left: 48px; width: 619px; top: 249px; }
  .field--blank { left: 48px; width: 619px; top: 298px; height: 28px; }
  .field__suffix {
    position: absolute; right: 0; bottom: 6px;
    font-size: 15px;
  }
  .appointment__notice {
    position: absolute;
    top: 350px; left: 0; right: 0;
    text-align: center;
    font-style: italic;
    font-size: 15px;
    color: var(--ink);
  }
</style>
</head>
<body>
  <section class="card card--front">
    <div class="brand">
      <span class="brand__dot"></span>
      <div class="brand__name">Harbourline<br>Physiotherapy</div>
    </div>
    <div class="contact">
      <p class="contact__name">Daniel Mercer</p>
      <p class="contact__role">CEO/Founder</p>
      <p class="contact__line"><span class="contact__label">Ph/Fax</span>02 9481 2057</p>
      <p class="contact__line">info@harbourlinephysio.example.com.au</p>
      <p class="contact__line">www.harbourlinephysio.example.com.au</p>
      <p class="contact__address">58 Wexley Lane Kelverton, NSW 2841</p>
    </div>
  </section>

  <section class="card card--back">
    <h2 class="appointment__title">Next Appointment</h2>
    <div class="field field--for">For :</div>
    <div class="field field--date">Date :</div>
    <div class="field field--time">Time :<span class="field__suffix">AM/PM</span></div>
    <div class="field field--doctor">With Dr :</div>
    <div class="field field--note">Note</div>
    <div class="field field--blank"></div>
    <p class="appointment__notice">If you are unable to keep your appointment please call the office 24 hours in advance.</p>
  </section>
</body>
</html>
```